Clinic for cellulit and fat removal

Name of clinic :
Lirava
- Body & Health (this has to be written on the site.)
I need CMS for me to be able to make changes myself.
A webpage for woman searching for a solution to remove fat and cellulit.
The owner is a brazilian woman in Denmark, and want her sense of aestetic shines thru the website.
There needs to be a slide show on the landing page showing big sliding pictures, of the clinic and and the treatments.
The Cryolipolysis, is a treatment freezing fat and cellulit, and this treatment will be the Attraction of the clinic.
Needs These pages in a horisontal fasion. (written in Danish)
Lirava
Behandlinger
- Cryolipolysis
- Trimflox
- Lymfemassage
- Korathelix
- Amberline Tide
Produkter
Priser
Kontakt
Clinic
Coded - Design and coding required
5+ page

```html
<!DOCTYPE html>
<html lang="da">
<head>
<meta charset="utf-8">
<title>Lirava – Body &amp; Health</title>
<link href="https://fonts.googleapis.com/css2?family=Lato:wght@300;400;700;900&display=swap" rel="stylesheet">
<style>
:root{
  --blue:#1fa3e8;
  --blue-dark:#137fc0;
  --ink:#333333;
  --ink-soft:#555555;
  --dark:#333333;
  --card-label:#3b3b3b;
  --white:#ffffff;
  --light:#f6f6f6;
}
*{box-sizing:border-box;margin:0;padding:0}
html,body{width:1200px;height:2889px;overflow:hidden;background:var(--white)}
body{font-family:'Lato',sans-serif;color:var(--ink);position:relative}
.abs{position:absolute}

/* top bar */
.topbar{position:absolute;left:0;top:0;width:1200px;height:67px;background:var(--blue)}
.lang{position:absolute;left:87px;top:16px;width:134px;height:36px;border:1px solid rgba(255,255,255,.6);color:#fff;font-size:13px;line-height:34px;padding-left:14px}
.lang::after{content:"";position:absolute;right:16px;top:14px;border:5px solid transparent;border-top-color:#fff}
.phone-box{position:absolute;left:836px;top:16px;width:130px;height:36px;border:1px solid rgba(255,255,255,.6);color:#fff;font-size:13px;line-height:34px;padding-left:10px;display:flex;align-items:center;gap:6px}
.social-box{position:absolute;left:976px;top:16px;width:138px;height:36px;border:1px solid rgba(255,255,255,.6);display:flex;align-items:center;justify-content:center;gap:9px}
.dot-icon{width:11px;height:11px;border-radius:50%;background:#fff}

/* hero */
.hero{position:absolute;left:0;top:67px;width:1200px;height:495px;overflow:hidden}
.hero-photo{position:absolute;inset:0;background:linear-gradient(100deg,#6f6e72 0%,#c9bdb5 30%,#e9e6e6 55%,#a59fb8 75%,#5b61a8 100%)}
.hero-shade{position:absolute;inset:0;background:rgba(20,20,30,.45)}
.logo{position:absolute;left:85px;top:22px;color:#fff;font-weight:900;font-size:30px;letter-spacing:.5px}
.nav{position:absolute;left:386px;top:30px;display:flex;gap:0;color:#fff;font-size:14px}
.nav span{margin-right:38px}
.nav-line{position:absolute;left:87px;top:82px;width:1026px;height:1px;background:rgba(255,255,255,.6)}
.btn-book{position:absolute;left:938px;top:21px;width:175px;height:36px;background:var(--blue);color:#fff;font-size:13px;text-align:center;line-height:36px}
.hero-title{position:absolute;left:0;top:178px;width:1200px;text-align:center;color:#fff;font-weight:900;font-size:55px;letter-spacing:1px}
.hero-text{position:absolute;left:255px;top:253px;width:690px;text-align:center;color:#fff;font-size:13px;line-height:24px}
.btn-hero{position:absolute;left:527px;top:333px;width:146px;height:47px;background:var(--blue-dark);color:#fff;font-size:13px;text-align:center;line-height:47px}
.arrow{position:absolute;top:268px}

/* section headings */
.sec-title{position:absolute;left:0;width:1200px;text-align:center;font-size:40px;font-weight:400;color:var(--ink);letter-spacing:1px}
.sec-rule{position:absolute;left:540px;width:120px;height:4px;background:var(--blue)}

/* treatment cards */
.card{position:absolute;top:728px;height:293px}
.card-img{position:absolute;left:0;top:0;width:100%;height:241px}
.card-label{position:absolute;left:0;top:241px;width:100%;height:52px;background:var(--card-label);color:#fff;font-size:17px;text-align:center;line-height:52px;letter-spacing:.5px}
.card-label.active{background:var(--blue)}
.pager{position:absolute;height:41px;background:#dcdcdc;border:1px solid #c8c8c8;display:flex;align-items:center;justify-content:center;gap:6px}
.pager i{width:10px;height:10px;border-radius:50%;background:#8fcdf0;display:block}
.pager i.on{background:var(--blue)}

/* about */
.about{position:absolute;left:0;top:1117px;width:1200px;height:790px;overflow:hidden}
.about-bg{position:absolute;inset:0;background:radial-gradient(ellipse at 50% 55%,#eeeae8 0%,#dedad9 45%,#d2d0d3 75%,#e6e4e6 100%)}
.about-text{position:absolute;left:240px;width:720px;text-align:center;font-size:13px;line-height:19.5px;color:var(--ink)}
.btn-about{position:absolute;left:535px;top:507px;width:130px;height:46px;background:var(--blue);color:#fff;font-size:13px;text-align:center;line-height:46px;box-shadow:2px 3px 6px rgba(0,0,0,.35)}

/* stories */
.stories-title{position:absolute;left:87px;top:1965px;font-size:42px;color:var(--ink);letter-spacing:.5px}
.stories-rule{position:absolute;left:87px;top:2027px;width:120px;height:4px;background:var(--blue)}
.stories-text{position:absolute;left:85px;top:2073px;width:530px;font-size:16px;line-height:26px;color:var(--ink-soft)}
.btn-more{position:absolute;left:87px;top:2211px;width:179px;height:58px;background:var(--blue);color:#fff;font-size:22px;text-align:center;line-height:58px;font-weight:400}
.polaroid{position:absolute;background:#fff;padding:13px 13px 30px;box-shadow:0 3px 10px rgba(0,0,0,.35)}
.polaroid .shot{width:100%;height:100%;background:linear-gradient(180deg,#e4e4e6 0%,#d4d4d8 55%,#b8bfcc 100%)}

/* footer */
.footer{position:absolute;left:0;top:2388px;width:1200px;height:501px;overflow:hidden}
.footer-base{position:absolute;left:0;top:40px;width:1200px;height:461px;background:var(--dark)}
.f-logo{position:absolute;left:86px;top:2600px;color:#fff;font-weight:900;font-size:56px;letter-spacing:1px}
.f-copy{position:absolute;left:87px;top:2680px;color:#fff;font-size:9px}
.f-head{position:absolute;top:2560px;color:#fff;font-size:17px;font-weight:700;letter-spacing:.5px}
.f-row{position:absolute;left:391px;color:#fff;font-size:11px;line-height:18px;display:flex;gap:18px}
.f-row svg{flex:none;margin-top:3px}
.f-social{position:absolute;left:391px;top:2726px;display:flex;gap:10px}
.f-social i{width:16px;height:16px;border-radius:50%;background:#fff;display:block}
.field{position:absolute;left:672px;width:237px;border:1px solid #666;color:#bbb;font-size:10px;padding:8px 10px}
.btn-send{position:absolute;left:672px;top:2779px;width:83px;height:31px;background:var(--blue);color:#fff;font-size:11px;text-align:center;line-height:31px}
.sitemap{position:absolute;left:978px;top:2597px;color:#ddd;font-size:10px;line-height:19px;list-style:none}
</style>
</head>
<body>

<header class="topbar">
  <div class="lang">ENGLISH</div>
  <div class="phone-box">
    <svg width="12" height="12" viewBox="0 0 24 24"><path fill="#fff" d="M6.6 10.8a15 15 0 0 0 6.6 6.6l2.2-2.2c.3-.3.7-.4 1-.2 1.1.4 2.3.6 3.6.6.6 0 1 .4 1 1V20c0 .6-.4 1-1 1A17 17 0 0 1 3 4c0-.6.4-1 1-1h3.5c.6 0 1 .4 1 1 0 1.2.2 2.4.6 3.6.1.3 0 .7-.2 1z"/></svg>
    <span>: 451-208-6734</span>
  </div>
  <div class="social-box"><i class="dot-icon"></i><i class="dot-icon"></i><i class="dot-icon"></i><i class="dot-icon"></i><i class="dot-icon"></i></div>
</header>

<section class="hero">
  <div class="hero-photo" role="img" aria-label="Slideshow image: woman relaxing during a cryolipolysis treatment at the clinic"></div>
  <div class="hero-shade"></div>
  <div class="logo">LIRAVA</div>
  <nav class="nav"><span>LIRAVA</span><span>BEHANDLINGER</span><span>PRODUKTER</span><span>PRISER</span><span>KONTAKT</span></nav>
  <div class="btn-book">BOOK APPOINTMENT</div>
  <div class="nav-line"></div>
  <h1 class="hero-title">BODY &amp; HEALTH</h1>
  <p class="hero-text">At vero eos et accusamus et iusto odio dignissimos ducimus qui blanditiis praesentium voluptatum deleniti atque corrupti quos dolores et quas molestias excepturi sint occaecati cupiditate non provident, similique sunt in culpa qui officia deserunt mollitia animi, id est laborum</p>
  <div class="btn-hero">READ MORE &gt;</div>
  <svg class="arrow" style="left:30px" width="20" height="34" viewBox="0 0 20 34"><path d="M16 3 3 17l13 14" fill="none" stroke="#fff" stroke-width="4"/></svg>
  <svg class="arrow" style="left:1148px" width="20" height="34" viewBox="0 0 20 34"><path d="M4 3l13 14L4 31" fill="none" stroke="#fff" stroke-width="4"/></svg>
</section>

<h2 class="sec-title" style="top:628px">BEHANDLINGER</h2>
<div class="sec-rule" style="top:691px"></div>

<div class="card" style="left:87px;width:250px">
  <div class="card-img" role="img" aria-label="Photo: cryolipolysis applicator on a client's abdomen" style="background:linear-gradient(135deg,#e8e8ea,#c9c6cc 60%,#7d86c6)"></div>
  <div class="card-label">CRYOLIPOLYSIS</div>
</div>
<div class="card" style="left:347px;width:248px">
  <div class="card-img" role="img" aria-label="Photo: waist with dotted contour lines" style="background:linear-gradient(180deg,#ececec,#d9b8a0 55%,#c89a7e)"></div>
  <div class="card-label">TRIMFLOX</div>
</div>
<div class="card" style="left:605px;width:248px">
  <div class="card-img" role="img" aria-label="Photo: lymphatic massage device on the thigh" style="background:linear-gradient(160deg,#6e5242,#c99a7e 45%,#e7cdbb)"></div>
  <div class="card-label active">LYMFEMASSAGE</div>
</div>
<div class="card" style="left:863px;width:250px">
  <div class="card-img" role="img" aria-label="Photo: hands giving a foot treatment" style="background:linear-gradient(150deg,#d8a58a,#e9c7b3 50%,#c48d72)"></div>
  <div class="card-label">KORATHELIX</div>
</div>

<div class="pager" style="left:555px;top:1057px;width:90px"><i></i><i class="on"></i><i></i></div>

<section class="about">
  <div class="about-bg" role="img" aria-label="Soft blurred photo of the clinic interior"></div>
  <svg class="abs" style="left:0;top:0" width="1200" height="200" viewBox="0 0 1200 200" preserveAspectRatio="none">
    <path d="M0 0H1200V75C1000 98 820 110 700 96 480 70 260-10 0 30Z" fill="var(--blue)"/>
    <path d="M0 0H1200V55C1000 80 820 92 700 78 480 55 260 10 0 55Z" fill="#fff"/>
  </svg>
  <h2 class="sec-title" style="top:145px">ABOUT LIRAVA</h2>
  <div class="sec-rule" style="top:210px"></div>
  <p class="about-text" style="top:253px">At vero eos et accusamus et iusto odio dignissimos ducimus qui blanditiis praesentium voluptatum deleniti atque corrupti quos dolores et quas molestias excepturi sint occaecati cupiditate non provident, similique sunt in culpa qui officia deserunt mollitia animi, id est laborum et dolorum fuga.</p>
  <p class="about-text" style="top:344px">Et harum quidem rerum facilis est et expedita distinctio. Nam libero tempore, cum soluta nobis est eligendi optio cumque nihil impedit quo minus id quod maxime placeat facere possimus, omnis voluptas assumenda est, omnis dolor repellendus. Temporibus autem quibusdam et aut officiis debitis aut rerum necessitatibus saepe eveniet ut et voluptates repudiandae sint et molestiae non recusandae. Itaque earum rerum hic tenetur a sapiente delectus, ut aut reiciendis voluptatibus maiores alias consequatur aut perferendis doloribus asperiores repellat</p>
  <div class="btn-about">Read More &gt;</div>
  <svg class="abs" style="left:0;top:590px" width="1200" height="200" viewBox="0 0 1200 200" preserveAspectRatio="none">
    <path d="M0 160C180 70 380 90 560 130 760 175 950 180 1200 120V200H0Z" fill="var(--blue)"/>
    <path d="M0 140C180 50 380 70 560 110 760 150 940 150 1200 100V200H0Z" fill="#fff"/>
    <path d="M600 160C800 185 1000 175 1200 150V200H600Z" fill="#fff"/>
  </svg>
</section>

<h2 class="stories-title">REAL PEOPLE, REAL STORIES</h2>
<div class="stories-rule"></div>
<p class="stories-text">At vero eos et accusamus et iusto odio dignissimos ducimus qui blanditiis praesentium voluptatum deleniti atque corrupti quos dolores et quas molestias excepturi sint occaecati cupiditate non provident,</p>
<div class="btn-more">SEE MORE</div>

<div class="polaroid" style="left:878px;top:2010px;width:232px;height:245px;transform:rotate(5deg)">
  <div class="shot" role="img" aria-label="Client photo after treatment"></div>
</div>
<div class="polaroid" style="left:672px;top:2060px;width:236px;height:242px;transform:rotate(-2deg)">
  <div class="shot" role="img" aria-label="Client photo before treatment"></div>
</div>
<div class="pager" style="left:847px;top:2336px;width:91px;height:39px"><i></i><i class="on"></i><i></i></div>

<footer class="footer">
  <div class="footer-base"></div>
  <svg class="abs" style="left:0;top:0" width="1200" height="140" viewBox="0 0 1200 140" preserveAspectRatio="none">
    <path d="M0 0C200-5 420 20 560 55 700 90 800 80 900 60L0 140Z" fill="var(--blue)"/>
    <path d="M0 0H1200V60C1050 90 850 140 640 110 470 80 300 30 0 30Z" fill="#fff"/>
  </svg>
</footer>

<div class="f-logo">LIRAVA</div>
<div class="f-copy">© Copyright 2017 Lirava | All Rights Reserved.</div>

<div class="f-head" style="left:391px">CONTACT US</div>
<div class="f-row" style="top:2605px">
  <svg width="9" height="12" viewBox="0 0 9 12"><path d="M4.5 0A4.5 4.5 0 0 0 0 4.5C0 8 4.5 12 4.5 12S9 8 9 4.5A4.5 4.5 0 0 0 4.5 0Zm0 6.2a1.7 1.7 0 1 1 0-3.4 1.7 1.7 0 0 1 0 3.4Z" fill="#fff"/></svg>
  <span>17 Solbakken Alle, Vejle<br>Syddanmark, 7100.</span>
</div>
<div class="f-row" style="top:2647px">
  <svg width="10" height="10" viewBox="0 0 24 24"><path fill="#fff" d="M6.6 10.8a15 15 0 0 0 6.6 6.6l2.2-2.2c.3-.3.7-.4 1-.2 1.1.4 2.3.6 3.6.6.6 0 1 .4 1 1V20c0 .6-.4 1-1 1A17 17 0 0 1 3 4c0-.6.4-1 1-1h3.5c.6 0 1 .4 1 1 0 1.2.2 2.4.6 3.6.1.3 0 .7-.2 1z"/></svg>
  <span>451-208-6734</span>
</div>
<div class="f-row" style="top:2677px">
  <svg width="11" height="9" viewBox="0 0 11 9"><rect width="11" height="9" rx="1" fill="#fff"/><path d="M0 1l5.5 4L11 1" fill="none" stroke="#333" stroke-width="1"/></svg>
  <span>hello@lirava-klinik.dk</span>
</div>
<div class="f-social"><i></i><i></i><i></i><i></i></div>

<div class="f-head" style="left:672px">ENQUIRE NOW</div>
<div class="field" style="top:2600px;height:37px">Name</div>
<div class="field" style="top:2650px;height:39px">Email</div>
<div class="field" style="top:2702px;height:60px">Message</div>
<div class="btn-send">SEND</div>

<div class="f-head" style="left:978px">SITEMAP</div>
<ul class="sitemap">
  <li>&gt; Lirava</li>
  <li>&gt; Behandlinger</li>
  <li>&gt; Produkter</li>
  <li>&gt; Priser</li>
  <li>&gt; Kontakt</li>
</ul>

</body>
</html>
```